Revamp Of Landing Page For an Automated AI Voice Agents Agency

here is my current landing page https://app.brightfernpromotionhub.biz/v2/preview/WXKRPmQ4hLzYBvNdTeGS?notrack=true

Please use all my current content and imagery of ai agents in your new design. Make it easy to ready, easy to navigate and easy to understand

I am looking for a SLEEK shiny polished looking website. I like Dark themed sites but am open to see light themed sites too so please dont be shy.

The site should have an Ai Voice Agent Theme about it. Maybe look and feel of futureistic but simple and not intimidating to the average person...

Here are a couple website designs I like for reference:
https://q7v.io/
https://ai-bots.marekholvin.com/
https://chatwelmo.com/ai-agents

Target Market(s)

b2b

Industry/Entity Type

AI Voice Agents

Coding

Coded - Design and coding required

Font styles to use
Other font styles liked:
• open

Requirements
Must have
• all elements and content and images used in existing design.
Nice to have
• open
Should not have
• open

```html
<!DOCTYPE html>
<html lang="en">
<head>
<meta charset="utf-8">
<title>Brightfern Promotion Hub – AI Voice Agents</title>
<link href="https://fonts.googleapis.com/css2?family=DM+Sans:wght@400;500;600;700&display=swap" rel="stylesheet">
<style>
:root{
  --ink:#111318;
  --text:#3a3d46;
  --muted:#5b5f6b;
  --blue:#1c50b4;
  --blue-deep:#1a55b8;
  --violet:#5a49e2;
  --violet-band:#4a37d8;
  --lilac:#efeefc;
  --line:#d9dcf2;
  --white:#ffffff;
  --footer:#111111;
}
*{box-sizing:border-box;margin:0;padding:0}
html,body{width:1200px;height:4073px;overflow:hidden}
body{position:relative;font-family:"DM Sans",sans-serif;color:var(--text);
  background:linear-gradient(180deg,#fff 0,#f4f4fd 600px,#fff 1100px,#f3f3fc 1500px,#fff 2000px,#f6f6fd 2380px,#fff 2760px,#f2f4fb 3300px,#eef1f9 3630px);}
.abs{position:absolute}
.frame{position:absolute;border:2px solid var(--blue);display:flex;align-items:center;justify-content:center;color:var(--blue);font-weight:600;background:transparent;white-space:nowrap}
.btn{position:absolute;display:flex;align-items:center;justify-content:center;gap:12px;font-weight:600;font-size:15px;text-transform:uppercase;border-radius:30px;letter-spacing:.01em}
.btn svg{width:26px;height:14px}
.btn-solid{background:linear-gradient(90deg,var(--violet),var(--blue));color:#fff}
.btn-outline{border:2px solid #fff;color:#fff}
.photo{position:absolute}

/* header */
.brand{left:144px;top:22px;display:flex;align-items:center;gap:10px;font-size:20px;font-weight:700;color:var(--blue)}
.brand-dot{width:18px;height:18px;border-radius:50%;background:var(--violet)}
.signin{left:926px;top:16px;width:129px;height:41px;font-size:14px}

/* hero */
.hero-photo{left:599px;top:73px;width:601px;height:439px;background:linear-gradient(135deg,#2c4fa5 0%,#6b8fd6 40%,#c6d2ee 70%,#3d5fb4 100%)}
.welcome{left:267px;top:157px;width:234px;height:47px;font-size:28px}
.hero-title{left:110px;top:212px;width:550px;font-size:55px;line-height:65px;font-weight:700;color:var(--ink);text-align:center;white-space:nowrap}
.hero-title span{background:#fff;padding:0 6px}
.hero-rule{left:320px;top:358px;width:130px;height:10px}
.hero-copy{left:138px;top:390px;width:494px;font-size:18px;line-height:29px;color:var(--text);text-align:center}
.hero-arc{left:-60px;top:458px;width:106px;height:240px}
.demo-main{left:387px;top:547px;width:305px;height:46px;border-radius:30px 0 0 30px;clip-path:polygon(0 0,100% 0,96% 100%,0 100%)}
.demo-book{left:688px;top:547px;width:161px;height:46px;border:2px solid var(--violet);color:var(--violet);border-radius:0 30px 30px 0;background:#fff}

/* workforce */
.work-title{left:272px;top:673px;width:654px;height:56px;font-size:34px}
.work-copy{left:130px;top:755px;width:940px;font-size:17px;line-height:32px;color:var(--text);text-align:center}
.agent{top:855px;width:289px;height:239px}
.agent-label{position:absolute;bottom:-16px;left:40px;right:40px;height:36px;background:#fff;display:flex;align-items:center;justify-content:center;font-size:16px;color:var(--ink);box-shadow:0 2px 8px rgba(0,0,0,.08)}
.agent-1{left:144px;background:linear-gradient(135deg,#cdd6e2,#7d8ea6 60%,#3e4a5d)}
.agent-2{left:455px;width:290px;background:linear-gradient(135deg,#1d3ea0,#3657c8)}
.agent-3{left:767px;background:linear-gradient(135deg,#9fb6d4,#dfe7f1 50%,#5b7aa3)}
.agent-card{left:476px;top:896px;width:248px;height:217px;background:#fff;border-bottom:4px solid var(--violet);box-shadow:0 6px 20px rgba(40,40,120,.15);text-align:center;padding-top:28px}
.agent-card h3{font-size:16px;font-weight:500;color:var(--ink)}
.agent-card p{font-size:13px;line-height:22px;margin-top:10px;color:var(--muted)}
.read-more{left:47px;top:148px;width:154px;height:42px;font-size:13px}
.arrow{width:36px;height:36px;border-radius:50%;display:flex;align-items:center;justify-content:center;top:956px}
.arrow-prev{left:91px;background:#3b3b3b}
.arrow-next{left:1071px;background:var(--blue)}

/* power */
.power-title{left:247px;top:1202px;width:706px;height:55px;font-size:34px}
.power-photo{left:0;top:1306px;width:545px;height:379px;background:linear-gradient(135deg,#4e5a74,#8fb1dd 45%,#3a4c6e 80%,#25282e)}
.wish{left:617px;top:1371px;width:460px}
.wish h3{font-size:20px;font-weight:600;color:var(--ink)}
.wish .lead{font-size:16.5px;line-height:28px;margin-top:12px;color:var(--text)}
.wish .body{font-size:12.5px;line-height:24px;margin-top:12px;color:var(--muted)}
.wish-btn{left:617px;top:1575px;width:268px;height:41px;font-size:13.5px}
.power-arc{left:950px;top:1585px;width:250px;height:160px}

/* employee */
.emp-title{position:absolute;left:144px;top:1766px;width:438px;height:120px;border:2px solid var(--blue);color:var(--blue);font-weight:600;font-size:34px;line-height:47px;padding:12px 16px;white-space:nowrap}
.feature{left:144px;width:438px;height:108px;background:#fff;box-shadow:0 4px 16px rgba(30,30,90,.08);display:flex;align-items:center;gap:22px;padding-left:24px}
.feature svg{width:58px;height:58px;flex:none}
.feature h4{font-size:18px;font-weight:500;color:var(--ink)}
.feature p{font-size:13px;color:var(--muted);margin-top:10px}
.emp-photo{left:651px;top:1744px;width:549px;height:553px;background:linear-gradient(135deg,#0c1c3a,#1d4e7a 45%,#6fb2d6 60%,#0b2342)}
.emp-blob{left:-100px;top:2150px;width:300px;height:180px}

/* hire band */
.hire{left:0;top:2390px;width:1200px;height:364px;background:linear-gradient(90deg,#5a35d9,var(--violet-band) 50%,#3f4bcb)}
.hire-title{left:275px;top:64px;width:650px;height:52px;font-size:34px;border-color:#fff;color:#fff}
.band-sub{left:0;width:1200px;text-align:center;color:#fff}
.hire-btn{left:466px;top:266px;width:268px;height:41px;font-size:13.5px}

/* promise */
.promise-title{left:425px;top:2828px;width:350px;height:54px;font-size:34px}
.dots{left:1035px;top:2830px;width:44px;height:42px}
.promise-card{top:2923px;width:438px;height:279px;border-radius:12px;color:#fff;display:flex;flex-direction:column;align-items:center;justify-content:center;text-align:center}
.promise-1{left:144px;background:linear-gradient(135deg,#1f4fa8,#2b5fb8 50%,#143c86)}
.promise-2{left:618px;width:437px;background:linear-gradient(135deg,#5b4ce6,#4c3fd8)}
.promise-card svg{width:62px;height:68px}
.promise-1 h3{font-size:24px;font-weight:400;line-height:40px;margin-top:18px}
.promise-2 h3{font-size:25px;font-weight:400;margin-top:12px}
.promise-2 p{font-size:17px;line-height:29px;margin-top:14px;opacity:.92}

/* questions */
.q-title{left:378px;top:3283px;width:443px;height:55px;font-size:34px}
.q-col{top:3375px;width:335px;height:217px;text-align:center;padding:38px 30px 0}
.q-col h4{font-size:17.5px;font-weight:500;line-height:28px;color:var(--ink)}
.q-col p{font-size:12.5px;line-height:23.5px;margin-top:14px;color:var(--muted)}
.q-1{left:108px}
.q-2{left:443px;background:#ececef}
.q-3{left:778px}

/* possibilities */
.possible{left:0;top:3630px;width:1200px;height:386px;background:var(--blue-deep)}
.possible-title{left:131px;top:65px;width:936px;height:120px;flex-direction:column;font-size:35px;line-height:56px;border-color:#fff;color:#fff}
.possible-btn{left:466px;top:284px;width:268px;height:43px;font-size:13.5px}

.footer{left:0;top:4016px;width:1200px;height:57px;background:var(--footer);color:#fff;font-size:12.5px;display:flex;align-items:center;justify-content:center}
</style>
</head>
<body>

<!-- header -->
<div class="abs brand"><span class="brand-dot"></span>Brightfern Promotion Hub</div>
<div class="btn btn-solid signin">Sign in
  <svg viewBox="0 0 26 14"><circle cx="19" cy="7" r="7" fill="none" stroke="#fff" stroke-width="1.4"/><path d="M2 7h19M17 3l4 4-4 4" fill="none" stroke="#fff" stroke-width="1.6"/></svg></div>

<!-- hero -->
<div class="photo hero-photo" role="img" aria-label="Robot and human call-centre agents wearing headsets at a desk with a glowing network overlay"></div>
<svg class="abs hero-arc" viewBox="0 0 106 240"><path d="M0 2a104 118 0 0 1 0 236" fill="none" stroke="#5547e0" stroke-width="4"/></svg>
<div class="frame welcome">WELCOME TO</div>
<h1 class="abs hero-title"><span>Brightfern</span><br><span>Promotion Hub</span></h1>
<svg class="abs hero-rule" viewBox="0 0 130 10"><line x1="0" y1="5" x2="56" y2="5" stroke="#1c50b4" stroke-width="3"/><circle cx="65" cy="5" r="5" fill="#5a49e2"/><line x1="74" y1="5" x2="130" y2="5" stroke="#1c50b4" stroke-width="3"/></svg>
<p class="abs hero-copy">Ai Voice Agents That Answer Calls, Book Appts, Send Emails, Text Messages, Follow Up Reminders, Transfer Calls &amp; More For You 24 Hours 7 Days A Week!</p>
<div class="btn btn-solid demo-main">Get an instant free demo
  <svg viewBox="0 0 26 14"><circle cx="19" cy="7" r="7" fill="none" stroke="#fff" stroke-width="1.4"/><path d="M2 7h19M17 3l4 4-4 4" fill="none" stroke="#fff" stroke-width="1.6"/></svg></div>
<div class="btn demo-book">Book a demo</div>

<!-- workforce -->
<h2 class="frame work-title">Meet Your New AI-Powered Workforce</h2>
<p class="abs work-copy">We Will Create An Ai Agent Customized For Your Business At No Cost. Simply Click The Button Above&amp;Your Very Own Ai Agent Will Be Calling You In Just A Couple Minutes, Experience The Magic&amp;Get Ready To Be Very Impressed!</p>
<div class="photo agent agent-1" role="img" aria-label="Sales agent with headset working at a laptop in a city office"><div class="agent-label">AI Sales Agent</div></div>
<div class="photo agent agent-2" role="img" aria-label="Blue backdrop for the receptionist agent"></div>
<div class="photo agent agent-3" role="img" aria-label="Humanoid robot with headset typing at a computer"><div class="agent-label">AI Appointment Setter</div></div>
<div class="abs agent-card">
  <h3>AI Receptionist</h3>
  <p>Takes Overflow &amp; After Hours<br>Calls or Can Take Calls 24/7<br>and Transfer To</p>
  <div class="btn btn-solid read-more">Read more
    <svg viewBox="0 0 26 14"><path d="M4 7h17M17 3l4 4-4 4" fill="none" stroke="#fff" stroke-width="1.6"/></svg></div>
</div>
<div class="abs arrow arrow-prev"><svg width="12" height="12" viewBox="0 0 12 12"><path d="M8 1L3 6l5 5" fill="none" stroke="#fff" stroke-width="2"/></svg></div>
<div class="abs arrow arrow-next"><svg width="12" height="12" viewBox="0 0 12 12"><path d="M4 1l5 5-5 5" fill="none" stroke="#fff" stroke-width="2"/></svg></div>

<!-- power -->
<h2 class="frame power-title">Install The Power of AI For Your Business</h2>
<div class="photo power-photo" role="img" aria-label="Hands at a laptop with floating holographic AI assistant panels"></div>
<div class="abs wish">
  <h3>YOUR WISH IS THEIR COMMAND</h3>
  <p class="lead">Your New Ai Agents Will Never Call In Sick<br>and Will Never Complain!</p>
  <p class="body">With your new team of AI Agents, handling inbound calls, sending emails and sms messages, booking appointments and handling customer service inquiries is going to save you a ton of time and money.</p>
</div>
<div class="btn btn-solid wish-btn">Get an instant free demo
  <svg viewBox="0 0 26 14"><circle cx="19" cy="7" r="7" fill="none" stroke="#fff" stroke-width="1.4"/><path d="M2 7h19M17 3l4 4-4 4" fill="none" stroke="#fff" stroke-width="1.6"/></svg></div>
<svg class="abs power-arc" viewBox="0 0 250 160"><path d="M100 160c40 -60 100 -70 150 -60V160z" fill="#ebe9fb"/><path d="M2 160C30 60 140 10 250 35" fill="none" stroke="#5a49e2" stroke-width="2"/></svg>

<!-- employee -->
<svg class="abs emp-blob" viewBox="0 0 300 180"><ellipse cx="130" cy="90" rx="180" ry="90" fill="#ecebf8"/></svg>
<h2 class="emp-title">An Employee That Never<br>Gets Sick!</h2>
<div class="abs feature" style="top:1918px">
  <svg viewBox="0 0 58 58" fill="none" stroke="#1c50b4" stroke-width="1.8"><path d="M20 12c-6 0-10 5-10 10-4 2-5 8-2 12-2 5 2 11 8 11 2 4 8 5 12 2V12c-3-3-6-2-8 0z"/><path d="M28 20h10M28 30h14M28 40h10"/><circle cx="41" cy="20" r="3"/><circle cx="45" cy="30" r="3"/><circle cx="41" cy="40" r="3"/></svg>
  <div><h4>Trained In Seconds</h4><p>Learns Your Entire Website In Seconds</p></div>
</div>
<div class="abs feature" style="top:2043px">
  <svg viewBox="0 0 58 58" fill="none" stroke="#1c50b4" stroke-width="1.8"><circle cx="29" cy="29" r="22"/><ellipse cx="29" cy="29" rx="10" ry="22"/><path d="M7 29h44M11 18h36M11 40h36"/></svg>
  <div><h4>Worldwide</h4><p>Works Anywhere In The Globe</p></div>
</div>
<div class="abs feature" style="top:2166px">
  <svg viewBox="0 0 58 58" fill="none" stroke="#1c50b4" stroke-width="1.8"><circle cx="29" cy="18" r="6"/><circle cx="29" cy="18" r="12" stroke-dasharray="5 4"/><circle cx="15" cy="40" r="4"/><circle cx="29" cy="40" r="4"/><circle cx="43" cy="40" r="4"/><path d="M8 54c0-5 3-8 7-8s7 3 7 8M22 54c0-5 3-8 7-8s7 3 7 8M36 54c0-5 3-8 7-8s7 3 7 8"/></svg>
  <div><h4>User-Friendly</h4><p>Your Ai Agents Sound As If They're Real Humans</p></div>
</div>
<div class="photo emp-photo" role="img" aria-label="Robotic hand shaking a human hand against glowing binary data"></div>

<!-- hire band -->
<section class="abs hire">
  <h2 class="frame hire-title">Our AI Agents Our Ready To Be Hired</h2>
  <p class="abs band-sub" style="top:148px;font-size:18px">Instant Answers, No Coffee, Bathroom Or Lunch Breaks Needed</p>
  <p class="abs band-sub" style="top:188px;font-size:12.5px;line-height:24px">We Will Create An Ai Agent Customized For Your Business At No Cost. Simply Click The Button Above And Your Very Own Ai Agent Will Be<br>Calling You In Just A Couple Minutes. Experience The Magic And Get Ready To Be Very Impressed!</p>
  <div class="btn btn-outline hire-btn">Get an instant free demo
    <svg viewBox="0 0 26 14"><circle cx="19" cy="7" r="7" fill="#fff" fill-opacity=".25"/><path d="M2 7h19M17 3l4 4-4 4" fill="none" stroke="#fff" stroke-width="1.6"/></svg></div>
</section>

<!-- promise -->
<h2 class="frame promise-title">Our Promise To You</h2>
<svg class="abs dots" viewBox="0 0 44 42" fill="#5a6fd0"><g id="dotrow"><circle cx="2" cy="2" r="1.6"/><circle cx="15" cy="2" r="1.6"/><circle cx="28" cy="2" r="1.6"/><circle cx="41" cy="2" r="1.6"/></g><use href="#dotrow" y="13"/><use href="#dotrow" y="26"/><use href="#dotrow" y="38"/></svg>
<div class="abs promise-card promise-1" role="img" aria-label="Blue-tinted photo of hands at a desk behind the guarantee">
  <svg viewBox="0 0 62 68" fill="none" stroke="#fff" stroke-width="2"><path d="M31 3l24 9v18c0 17-10 29-24 35C17 59 7 47 7 30V12z"/><path d="M31 11l17 6v13c0 12-7 21-17 26-10-5-17-14-17-26V17z"/><path d="M21 33l7 7 14-14"/></svg>
  <h3>14-Day Money Back<br>Guarantee</h3>
</div>
<div class="abs promise-card promise-2">
  <svg viewBox="0 0 62 68" fill="none" stroke="#fff" stroke-width="2"><circle cx="31" cy="34" r="28"/><path d="M18 36v-6a13 13 0 0 1 26 0v6"/><rect x="14" y="34" width="7" height="12" rx="3"/><rect x="41" y="34" width="7" height="12" rx="3"/><path d="M44 46c0 5-5 8-11 8"/></svg>
  <h3>24/7 Customer Support</h3>
  <p>Often Praised For Our Friendly &amp; Helpful<br>Support Team</p>
</div>

<!-- questions -->
<h2 class="frame q-title">Do You Have Questions?</h2>
<div class="abs q-col q-1"><h4>What Exactly are The AI<br>Voice Agents?</h4><p>AI Voice Agents are specialized human sounding bots, having smart and masterful conversations and each is expertly</p></div>
<div class="abs q-col q-2"><h4>How Will these AI Voice<br>Agents benefit</h4><p>Ai Voice Agents Answer Calls, Book Appts, Send Emails, Text Messages, Follow Up Reminders &amp; More For You 24/7!</p></div>
<div class="abs q-col q-3"><h4>Are They Easy to Use?</h4><p>We provide a done for you service. We create your AI Voice Agent and launch it within days!</p></div>

<!-- possibilities -->
<section class="abs possible">
  <h2 class="frame possible-title"><span>These AI Agents Can Help Your Business Tremendously</span><span>Imagine The Possibilities</span></h2>
  <p class="abs band-sub" style="top:210px;font-size:12.5px;line-height:24px">We Will Create An Ai Agent Customized For Your Business At No Cost. Simply Click The Button Above And Your Very Own Ai Agent Will Be<br>Calling You In Just A Couple Minutes. Experience The Magic And Get Ready To Be Very Impressed!</p>
  <div class="btn btn-outline possible-btn">Get an instant free demo
    <svg viewBox="0 0 26 14"><circle cx="19" cy="7" r="7" fill="#fff" fill-opacity=".25"/><path d="M2 7h19M17 3l4 4-4 4" fill="none" stroke="#fff" stroke-width="1.6"/></svg></div>
</section>

<footer class="abs footer">Copyright © 2025 Company Name - All Rights Reserved - Privacy | Terms &amp; Conditions | Earnings &amp; Products Disclaimer</footer>

</body>
</html>
```